Im open to ideas.. I was thinking on my business cards aswell as my logo. a place for my name. email. phone number and abn..

ive attched a file with my business logo. which i dont love the colours.. i was think a dark background with charcoal letters so something along those colour schumes but im open to ideas..

BRM Constructions

```html
<!DOCTYPE html>
<html lang="en">
<head>
<meta charset="utf-8">
<title>BRM Constructions – Business Card</title>
<link rel="stylesheet" href="https://fonts.googleapis.com/css2?family=Lato:wght@400;700;900&display=swap">
<style>
  :root {
    --backdrop: #1c1c1c;
    --card: #ffffff;
    --card-shade: #f1f1f1;
    --charcoal: #1d1d1d;
    --ink: #3a3a3a;
    --red: #c8161d;
    --red-deep: #9e0f15;
  }
  * { margin: 0; padding: 0; box-sizing: border-box; }
  html, body {
    width: 1200px;
    height: 873px;
    overflow: hidden;
    background: var(--backdrop);
    font-family: "Lato", sans-serif;
  }
  .canvas {
    position: relative;
    width: 1200px;
    height: 873px;
  }
  .business-card {
    position: absolute;
    left: 180px;
    top: 196px;
    width: 840px;
    height: 480px;
    background: linear-gradient(160deg, var(--card) 0%, var(--card-shade) 100%);
    overflow: hidden;
  }
  .card-band {
    position: absolute;
    inset: 0;
    width: 100%;
    height: 100%;
  }
  .brand-name {
    position: absolute;
    left: 220px;
    top: 118px;
    display: flex;
    align-items: center;
    gap: 14px;
    font-weight: 900;
    font-size: 42px;
    letter-spacing: 1px;
    text-transform: uppercase;
    color: var(--charcoal);
    white-space: nowrap;
  }
  .brand-square {
    width: 26px;
    height: 26px;
    background: var(--red);
  }
  .owner {
    position: absolute;
    right: 60px;
    top: 200px;
    text-align: right;
  }
  .owner-name {
    font-weight: 700;
    font-size: 22px;
    color: var(--red);
  }
  .owner-role {
    font-size: 15px;
    color: var(--ink);
    margin-top: 2px;
  }
  .contact-list {
    position: absolute;
    left: 58px;
    top: 268px;
    list-style: none;
  }
  .contact-item {
    display: flex;
    align-items: center;
    gap: 10px;
    font-size: 18px;
    color: var(--ink);
    height: 32px;
    white-space: nowrap;
  }
  .contact-icon {
    width: 18px;
    height: 18px;
    fill: var(--red);
  }
  .contact-label {
    width: 18px;
    font-weight: 700;
    font-size: 11px;
    color: var(--red);
  }
  .contact-web {
    font-weight: 700;
    font-size: 20px;
    color: var(--red);
    margin-top: 6px;
  }
</style>
</head>
<body>
  <main class="canvas">
    <section class="business-card" aria-label="BRM Constructions business card">
      <svg class="card-band" viewBox="0 0 840 480" preserveAspectRatio="none" aria-hidden="true">
        <path d="M0,446 C300,456 600,384 840,262 L840,480 L0,480 Z" fill="var(--red-deep)"/>
        <path d="M0,456 C310,464 610,396 840,280 L840,480 L0,480 Z" fill="var(--red)"/>
      </svg>

      <div class="brand-name">
        <span class="brand-square"></span>
        <span>BRM Constructions</span>
      </div>

      <div class="owner">
        <p class="owner-name">Daniel Harlow</p>
        <p class="owner-role">Owner / Founder</p>
      </div>

      <ul class="contact-list">
        <li class="contact-item">
          <svg class="contact-icon" viewBox="0 0 24 24" aria-hidden="true">
            <path d="M3 7c0-2 2-3 9-3s9 1 9 3v2h-4V7.5c-1-.5-3-.8-5-.8s-4 .3-5 .8V9H3z"/>
            <path d="M6 10h12l2 9H4z"/>
          </svg>
          <span>0412555018</span>
        </li>
        <li class="contact-item">
          <svg class="contact-icon" viewBox="0 0 24 24" aria-hidden="true">
            <path d="M2 5h20v14H2z M3.5 6.5 12 13l8.5-6.5" stroke="#fff" stroke-width="1.4"/>
          </svg>
          <span>info@brmconstructions.com</span>
        </li>
        <li class="contact-item">
          <span class="contact-label">ABN</span>
          <span>12 345 678 901</span>
        </li>
        <li class="contact-item contact-web">www.brmconstructions.com</li>
      </ul>
    </section>
  </main>
</body>
</html>
```